Maple Roster Business Card for recruitment company

We are looking for a Business Card Design that incorporates our personal details and our busines name and logo. We are a specialized search consultancy that recruit Property and Construction professionals.
We would like a business card that stands out and is appealing to the Construction and Property industry as well.

Target Market(s)

people in the construction and property industry

Contact Information for Business Card

Business Name and logo

Font styles to use
Serif

Colors
0094D4
00A9DD
6FCCEA
C7EBF8
E9F6FB

Requirements
Must have
• Business name and logo as well as contact details
Should not have
• No photos of us please

```html
<!DOCTYPE html>
<html lang="en">
<head>
<meta charset="utf-8">
<title>Maple Roster Business Card</title>
<link href="https://fonts.googleapis.com/css2?family=Questrial&family=Montserrat:wght@700&display=swap" rel="stylesheet">
<style>
  :root {
    --backdrop: #2b2c2d;
    --card-white: #fbfbfb;
    --ink-navy: #0b3a4f;
    --card-navy: #06344a;
    --text-grey: #3c3c3c;
    --on-navy: #ececec;
  }
  * { margin: 0; padding: 0; box-sizing: border-box; }
  html, body {
    width: 1200px; height: 732px; overflow: hidden;
    background: var(--backdrop);
  }
  .canvas { position: relative; width: 1200px; height: 732px; }
  .card {
    position: absolute; top: 242px; width: 436px; height: 248px;
    box-shadow: 0 8px 18px rgba(0,0,0,0.45);
  }
  .card-front {
    left: 144px;
    background: linear-gradient(135deg, #ffffff 0%, var(--card-white) 60%, #efefef 100%);
  }
  .card-back {
    left: 621px;
    background: linear-gradient(135deg, #083a50 0%, var(--card-navy) 70%, #042f43 100%);
    display: flex; align-items: center; justify-content: center;
  }
  .wordmark {
    position: absolute; left: 15px; top: 19px;
    font-family: "Questrial", sans-serif;
    font-size: 35px; letter-spacing: 1px; line-height: 1;
    color: var(--ink-navy);
  }
  .holder {
    position: absolute; left: 15px; bottom: 13px;
    font-family: "Questrial", sans-serif;
    font-size: 12.8px; line-height: 14.2px; color: var(--text-grey);
  }
  .holder-name {
    font-family: "Montserrat", sans-serif; font-weight: 700;
    font-size: 16px; line-height: 18px; color: var(--ink-navy);
    margin-bottom: 1px;
  }
  .contacts {
    position: absolute; right: 15px; bottom: 13px;
    list-style: none; text-align: right;
    font-family: "Questrial", sans-serif;
    font-size: 12.8px; line-height: 14.2px; color: var(--text-grey);
  }
  .contact-label {
    font-weight: 700; color: var(--ink-navy); margin-left: 6px;
    display: inline-block; width: 12px; text-align: left;
  }
  .back-mark {
    font-family: "Questrial", sans-serif;
    font-size: 34px; letter-spacing: 1px; color: var(--on-navy);
  }
</style>
</head>
<body>
<main class="canvas">
  <section class="card card-front">
    <div class="wordmark">MAPLE ROSTER</div>
    <div class="holder">
      <p class="holder-name">Claire Whitford</p>
      <p class="holder-role">Director | Senior Search Consultant</p>
      <p class="holder-city">Auckland, New Zealand</p>
    </div>
    <ul class="contacts">
      <li>+64 21 555 0142<span class="contact-label">:T</span></li>
      <li>claire@mapleroster.nz<span class="contact-label">:E</span></li>
      <li>www.mapleroster.nz<span class="contact-label">:W</span></li>
    </ul>
  </section>
  <section class="card card-back">
    <div class="back-mark">MAPLE ROSTER</div>
  </section>
</main>
</body>
</html>
```